Stationery for a private security company, "Brenmoor Security Services Ltd."

Needed is a stationery design for a private security company. The designs must show professionalism and that our company mean nothing but business. Watermark of the company logo on the letterhead page is also a must. The final design must represent innovation and professionalism. It would be great if designers could integrate the colours black and silver onto the cards and letterheads..

Thank you

```html
<!DOCTYPE html>
<html lang="en">
<head>
<meta charset="utf-8">
<title>Brenmoor Security Services Ltd. — Stationery</title>
<link rel="stylesheet" href="https://fonts.googleapis.com/css2?family=Arimo:wght@400;700&display=swap">
<style>
  :root {
    --stage: #000000;
    --paper: #ffffff;
    --band-dark: #3a3a3a;
    --band-mid: #6e6e70;
    --band-light: #8f8f92;
    --silver: #e9e9ea;
    --ink-light: #ffffff;
    --watermark: #e6e6e6;
    --card-edge: #d8d8d8;
  }
  * { margin: 0; padding: 0; box-sizing: border-box; }
  html, body { width: 848px; height: 1200px; overflow: hidden; background: var(--stage); }
  body { font-family: "Arimo", Arial, sans-serif; position: relative; }

  .letterhead {
    position: absolute; left: 124px; top: 36px;
    width: 600px; height: 848px;
    background: var(--paper); overflow: hidden;
  }
  .letterhead__art { position: absolute; inset: 0; width: 100%; height: 100%; }
  .letterhead__name {
    position: absolute; top: 14px; left: 0; width: 100%;
    text-align: center; color: var(--ink-light);
    font-weight: 700; font-size: 33px; letter-spacing: -0.5px;
  }
  .letterhead__title {
    position: absolute; top: 52px; left: 0; width: 100%;
    text-align: center; color: var(--silver);
    font-size: 16px; padding-left: 0;
  }
  .letterhead__watermark {
    position: absolute; top: 560px; left: 0; width: 100%;
    text-align: center; color: var(--watermark);
    font-weight: 700; line-height: 1.15;
  }
  .letterhead__watermark-mark {
    width: 140px; height: 140px; border-radius: 50%;
    background: #f3f3f3; margin: 0 auto 24px;
  }
  .letterhead__watermark-name { font-size: 22px; letter-spacing: 1px; }
  .letterhead__watermark-sub { font-size: 20px; letter-spacing: 1px; }
  .letterhead__contact {
    position: absolute; left: 8px; top: 800px;
    color: var(--ink-light); font-size: 11.5px; line-height: 1.15;
  }
  .letterhead__contact .mobile { font-size: 10px; }

  .card {
    position: absolute; left: 214px; top: 924px;
    width: 420px; height: 240px;
    border: 3px solid var(--card-edge);
    background:
      radial-gradient(ellipse 55% 60% at 60% 45%, var(--band-light) 0%, var(--band-mid) 45%, var(--band-dark) 100%);
    overflow: hidden; color: var(--ink-light);
  }
  .card__stripe {
    position: absolute; left: 0; top: 30px; width: 100%; height: 12px;
    background: rgba(255,255,255,0.08);
  }
  .card__divider {
    position: absolute; left: 150px; top: 0; width: 3px; height: 100%;
    background: linear-gradient(to bottom, #2a2a2a, #d9d9d9 30%, #6a6a6a 60%, #1e1e1e);
  }
  .card__brand { position: absolute; left: 120px; top: 48px; display: flex; align-items: center; gap: 8px; }
  .card__brand-mark { width: 20px; height: 20px; border-radius: 50%; background: var(--silver); }
  .card__brand-name { font-size: 17px; line-height: 1; }
  .card__brand-sub { font-size: 7.5px; display: block; margin-top: 3px; }
  .card__person { position: absolute; left: 18px; top: 176px; }
  .card__person-name { font-weight: 700; font-size: 18px; letter-spacing: -0.3px; }
  .card__person-title { font-size: 9px; margin-left: 12px; }
  .card__contact {
    position: absolute; left: 190px; top: 150px;
    font-size: 9.5px; line-height: 1.2;
  }
  .card__contact .mobile { font-size: 8px; }
</style>
</head>
<body>
  <section class="letterhead" aria-label="Letterhead">
    <svg class="letterhead__art" viewBox="0 0 727 1027" preserveAspectRatio="none" aria-hidden="true">
      <defs>
        <radialGradient id="bandGlow" cx="0.5" cy="0.55" r="0.7">
          <stop offset="0" stop-color="#8f8f92"/>
          <stop offset="0.5" stop-color="#6a6a6c"/>
          <stop offset="1" stop-color="#3a3a3a"/>
        </radialGradient>
      </defs>
      <!-- header band with skyline edge -->
      <path fill="url(#bandGlow)" d="M0 0 H727 V155 H672 V190 H528 V166 H416 V178 H372 V180 H278 V178 H121 V182 H47 V182 H0 Z"/>
      <g fill="#ffffff">
        <rect x="47" y="112" width="74" height="70"/>
        <rect x="246" y="125" width="32" height="53"/>
        <rect x="372" y="112" width="44" height="68"/>
        <rect x="495" y="97" width="33" height="69"/>
        <rect x="610" y="106" width="62" height="49"/>
      </g>
      <rect x="0" y="144" width="727" height="12" fill="#ffffff" opacity="0.18"/>
      <!-- footer band with skyline edge -->
      <path fill="url(#bandGlow)" d="M0 883 H71 V923 H132 V850 H210 V886 H320 V862 H454 V910 H485 V882 H607 V923 H679 V858 H727 V1027 H0 Z"/>
      <rect x="0" y="920" width="727" height="10" fill="#ffffff" opacity="0.12"/>
    </svg>

    <h1 class="letterhead__name">ROHAN MEHTA</h1>
    <p class="letterhead__title">GRAPHIC DESIGNER</p>

    <div class="letterhead__watermark">
      <div class="letterhead__watermark-mark"></div>
      <div class="letterhead__watermark-name">BRENMOOR</div>
      <div class="letterhead__watermark-sub">SECURITY SERVICES LTD.</div>
    </div>

    <address class="letterhead__contact" style="font-style:normal">
      <div>B-12 LAKEVIEW ENCLAVE SECTOR 9 (NDA)</div>
      <div class="mobile">MOBILE- +919800412736</div>
      <div>email-rohanmehta.design@mail.com</div>
    </address>
  </section>

  <section class="card" aria-label="Business card">
    <div class="card__stripe"></div>
    <div class="card__divider"></div>
    <div class="card__brand">
      <span class="card__brand-mark"></span>
      <span class="card__brand-name">BRENMOOR<span class="card__brand-sub">SECURITY SERVICES LTD.</span></span>
    </div>
    <div class="card__person">
      <div class="card__person-name">ROHAN MEHTA</div>
      <div class="card__person-title">GRAPHIC DESIGNER</div>
    </div>
    <address class="card__contact" style="font-style:normal">
      <div>B-12 LAKEVIEW ENCLAVE SECTOR 9 (NDA)</div>
      <div class="mobile">MOBILE- +919800412736</div>
      <div>email-rohanmehta.design@mail.com</div>
    </address>
  </section>
</body>
</html>
```